Business Card Design

We are a manufacturing and distribution company with most of our customer base being supermarkets. We have established brand guidelines that are attached.

```html
<!DOCTYPE html>
<html lang="en">
<head>
<meta charset="utf-8">
<title>Veltrano Business Card</title>
<link rel="stylesheet" href="https://fonts.googleapis.com/css2?family=Archivo:wdth,wght@62..125,500;62..125,700&family=Arimo:wght@400&display=swap">
<style>
  :root {
    --bg: #b8b8b8;
    --red: #e41b23;
    --blue: #0069ad;
    --white: #ffffff;
    --ink-dark: #231f20;
  }
  * { margin: 0; padding: 0; box-sizing: border-box; }
  html, body {
    width: 1075px; height: 1200px; overflow: hidden;
    background: var(--bg);
  }
  .canvas { position: relative; width: 1075px; height: 1200px; }
  .card {
    position: absolute; left: 206px; width: 663px; height: 395px;
  }
  .card-front { top: 187px; background: var(--white); }
  .card-back { top: 637px; background: var(--ink-dark); }

  .header-bands { position: absolute; left: 0; top: 0; width: 663px; height: 105px; }

  .brand-name {
    position: absolute; left: 33px; top: 44px;
    font-family: "Archivo", sans-serif; font-stretch: 125%; font-weight: 700;
    font-size: 41px; line-height: 1; color: var(--white); letter-spacing: 0.5px;
  }
  .person { position: absolute; left: 35px; top: 225px; }
  .person-name {
    font-family: "Archivo", sans-serif; font-weight: 700; font-stretch: 100%;
    font-size: 22px; line-height: 1; color: var(--red);
  }
  .person-title {
    font-family: "Arimo", sans-serif; font-size: 16px; line-height: 1;
    color: var(--blue); margin-top: 4px;
  }
  .contacts { position: absolute; left: 35px; top: 302px; list-style: none; }
  .contacts li {
    display: flex; align-items: center; height: 24px;
    font-family: "Arimo", sans-serif; font-size: 18px; color: var(--blue);
  }
  .contacts svg { width: 17px; height: 17px; margin-right: 6px; flex: none; }
  .address {
    position: absolute; right: 40px; top: 328px; text-align: right;
    font-family: "Arimo", sans-serif; font-size: 18px; line-height: 24px; color: var(--blue);
  }
  .back-name {
    position: absolute; left: 0; right: 0; top: 226px; text-align: center;
    font-family: "Archivo", sans-serif; font-stretch: 125%; font-weight: 700;
    font-size: 54px; line-height: 1; color: var(--white); letter-spacing: 1px;
  }
</style>
</head>
<body>
<div class="canvas">
  <section class="card card-front">
    <svg class="header-bands" viewBox="0 0 663 105" aria-hidden="true">
      <polygon points="0,0 455,0 296,105 0,105" fill="var(--red)"/>
      <polygon points="455,0 663,0 663,105 611,105" fill="var(--blue)"/>
    </svg>
    <div class="brand-name">VELTRANO</div>

    <div class="person">
      <div class="person-name">MARCUS HALE</div>
      <div class="person-title">MANAGING DIRECTOR</div>
    </div>

    <ul class="contacts">
      <li>
        <svg viewBox="0 0 24 24" aria-hidden="true"><path fill="var(--red)" d="M6.6 10.8a15 15 0 0 0 6.6 6.6l2.2-2.2a1 1 0 0 1 1-.25 11.4 11.4 0 0 0 3.6.57 1 1 0 0 1 1 1V20a1 1 0 0 1-1 1A17 17 0 0 1 3 4a1 1 0 0 1 1-1h3.5a1 1 0 0 1 1 1c0 1.25.2 2.45.57 3.57a1 1 0 0 1-.25 1z"/></svg>
        044-987 654 321
      </li>
      <li>
        <svg viewBox="0 0 24 24" aria-hidden="true"><rect x="2" y="5" width="20" height="14" fill="var(--red)"/><path d="M2 5l10 8 10-8" fill="none" stroke="var(--white)" stroke-width="1.6"/></svg>
        info@veltrano.com
      </li>
      <li>
        <svg viewBox="0 0 24 24" aria-hidden="true"><g fill="none" stroke="var(--red)" stroke-width="2"><circle cx="12" cy="12" r="9.5"/><ellipse cx="12" cy="12" rx="4" ry="9.5"/><path d="M2.5 12h19M4 7h16M4 17h16"/></g></svg>
        www.veltrano.com
      </li>
    </ul>

    <div class="address">
      17, Harbour Road Unit 4<br>
      30218, Eastmoor
    </div>
  </section>

  <section class="card card-back">
    <div class="back-name">VELTRANO</div>
  </section>
</div>
</body>
</html>
```